Brochure Front Page Design Project

We need concepts for the front page of a clients brochure (A4 Portrait)
The client is a power products distributor (Lawnmowers, Trimmers, Blowers etc) and are looking for a clean fresh brochure.

No restrictions, any colours, full use of images, line art or renderings - lets see what we can generate.

Best concept wins!
Updates

The clients have advised they would like to see some concepts with an aesthetic similar to the following linkĀ http://www.brennolt.com/au/products/trimmers-brushcutters/

Industry/Entity Type

Distributor

Requirements
Must have
• Must incorporate their logo

Product Images (More images available from their site http://www.quillarvex.com.au/)
Nice to have
• The clients have advised they would like to see some concepts utilizing Black simple designs as well - similar to http://www.brennolt.com/au/products/trimmers-brushcutters/

```html
<!DOCTYPE html>
<html lang="en">
<head>
<meta charset="utf-8">
<title>QVX Power Products Brochure Cover</title>
<link rel="stylesheet" href="https://fonts.googleapis.com/css2?family=Exo+2:ital,wght@0,400;0,800;1,400&display=swap">
<style>
  :root {
    --stage: #3a3a3a;
    --page-light: #ffffff;
    --page-shade: #dfe1e4;
    --brand-green: #5cb531;
    --brand-blue: #2a82c8;
    --brand-navy: #1b3f8a;
    --logo-grey: #8a8c8f;
    --ink: #222222;
    --photo-grass: #4f7a36;
    --photo-grass-dark: #2f4d22;
    --photo-sky: #a9b6a2;
  }
  * { box-sizing: border-box; margin: 0; padding: 0; }
  html, body { width: 880px; height: 1200px; overflow: hidden; }
  body { background: var(--stage); font-family: "Exo 2", sans-serif; position: relative; }

  .cover {
    position: absolute; left: 45px; top: 30px; width: 790px; height: 1140px;
    background: radial-gradient(ellipse at 50% 45%, var(--page-light) 45%, var(--page-shade) 100%);
    overflow: hidden;
  }

  .header-band {
    position: absolute; left: 0; top: 150px; width: 350px; height: 38px;
    background: var(--brand-green);
    color: #fff; font-size: 14px; font-style: italic; letter-spacing: 1.5px;
    line-height: 38px; padding-left: 40px; text-transform: uppercase;
  }
  .header-stripes { position: absolute; left: 340px; top: 150px; }

  .brand-name {
    position: absolute; right: 45px; top: 88px;
    font-weight: 800; font-size: 120px; line-height: 1; letter-spacing: 4px;
    color: var(--logo-grey);
  }

  .photo {
    position: absolute;
    border: 4px solid #fff;
    box-shadow: 0 3px 8px rgba(0,0,0,0.35);
  }
  .photo--trimmer { left: 59px; top: 345px; width: 330px; height: 230px;
    background: linear-gradient(160deg, var(--photo-sky) 0%, var(--photo-grass) 45%, var(--photo-grass-dark) 100%); }
  .photo--mower-side { left: 410px; top: 345px; width: 230px; height: 230px;
    background: linear-gradient(180deg, #8e9c86 0%, var(--photo-grass) 55%, var(--photo-grass-dark) 100%); }
  .photo--mower-front { left: 119px; top: 590px; width: 270px; height: 155px;
    background: linear-gradient(180deg, #6f8a5c 0%, #7b8a78 45%, var(--photo-grass) 100%); }
  .photo--mower-angle { left: 410px; top: 590px; width: 325px; height: 225px;
    background: linear-gradient(170deg, #5d7a45 0%, #6f6f6f 45%, var(--photo-grass) 100%); }

  .tagline {
    position: absolute; left: 0; right: 0; top: 875px;
    text-align: center; font-style: italic; font-size: 27px; color: var(--ink);
  }

  .footer-band { position: absolute; left: 0; top: 1075px; width: 790px; height: 50px; }
  .footer-url {
    position: absolute; left: 75px; top: 1075px; height: 50px; line-height: 50px;
    color: #fff; font-size: 16px; letter-spacing: 3px;
  }
  .footer-brand {
    position: absolute; right: 40px; top: 1077px; height: 46px; line-height: 46px;
    color: #fff; font-weight: 800; font-size: 40px; letter-spacing: 2px;
  }
</style>
</head>
<body>
  <main class="cover">
    <div class="header-band">Power Product Specialists</div>
    <svg class="header-stripes" width="120" height="38" viewBox="0 0 120 38">
      <polygon points="20,0 40,0 20,38 0,38" fill="#2a82c8"/>
      <polygon points="48,0 60,0 40,38 28,38" fill="#2a82c8"/>
      <polygon points="68,0 80,0 60,38 48,38" fill="#2a82c8"/>
      <polygon points="88,0 100,0 80,38 68,38" fill="#2a82c8"/>
    </svg>
    <div class="brand-name">QVX</div>

    <div class="photo photo--trimmer" role="img" aria-label="Person edging a lawn with a petrol line trimmer"></div>
    <div class="photo photo--mower-side" role="img" aria-label="Rotary lawnmower being pushed across grass"></div>
    <div class="photo photo--mower-front" role="img" aria-label="Front view of a lawnmower on a lawn"></div>
    <div class="photo photo--mower-angle" role="img" aria-label="Close view of a lawnmower engine and deck on grass"></div>

    <p class="tagline">QVX Power products - Made to Last</p>

    <svg class="footer-band" width="790" height="50" viewBox="0 0 790 50">
      <defs>
        <linearGradient id="footerBlue" x1="0" y1="0" x2="1" y2="0">
          <stop offset="0" stop-color="#2a82c8"/>
          <stop offset="1" stop-color="#1b3f8a"/>
        </linearGradient>
      </defs>
      <polygon points="0,0 520,0 495,50 0,50" fill="#5cb531"/>
      <polygon points="530,0 790,0 790,50 505,50" fill="url(#footerBlue)"/>
    </svg>
    <div class="footer-url">www.quillarvex.com.au</div>
    <div class="footer-brand">QVX</div>
  </main>
</body>
</html>
```